Business Card Design for Vintage Jazz

I am a vintage jazz band leader in New York City. My groups play the music of the 1920s, 1930s and 1940s. My website is morvalquist.com for more info on what I do.

I am looking for a two sided business card design that has the look and feel of a really nice business card from the 1930s. I need to convey with the design that my work has that vintage kind of class and style, but also conveys that we are fun and entertaining.

Most importantly it should make a bold staement. If Hal Denbrook had a card, what would it have looked like? I want a card that I feel confident will make an impact and will let people know that my work is te the top that NYC has to offer in vintage jazz..

Note that I have only decided to avoid the "committed payment" option as I have not used this service before. Assuming that I get quality work I will select a design from those presented.

Target Market(s)

people who want to hire my band for events, media, and new fans of the band

Industry/Entity Type

Performing Art

Contact Information for Business Card

Definitely a matte finish, possibly a sort of old style of paper with that brown tint? definitely a thick card.

Requirements
Must have
• FRONT
• My name: Tobin Vashley
• What I do: Bandleader, Guitarist, Vocalist, Songwriter
• Contact Details: morvalquist.com tobin@morvalquist.com 646-555-0148
• BACK
• My Social Media Links:
• facebook.morvalquist.com
• twitter, instagram, linkedin: morvalquist
• I'm also including a photo image I would like to use. The photo's background is not needed, and to be honest isn't really desireable. Just looking to use the image of me.
Nice to have
• I'm attaching which could be used as is, omitted from the card, or altered maybe with text going around the outside of the circle or in some other way. It may need some clean up to the edges of the lettering as we only use it for the website thumbnail.
• If there's space I'd like to include the text "join our mailing list for a free song download: freesong.morvalquist.com" If not perhaps just "Download a Free Song at: freesong.morvalquist.com - something to this end.
Should not have
• anything cartoony. Don't think retro 90s's vision of the swing era, think actual swing era!
• anything modern. Got to look old school
• Try to avoid dark backgrounds. Since we often play in bars and clubs where it is dar, a d
• avoid script fonts.

```html
<!DOCTYPE html>
<html lang="en">
<head>
<meta charset="utf-8">
<title>Tobin Vashley — Business Card</title>
<link rel="stylesheet" href="https://fonts.googleapis.com/css2?family=Open+Sans:wght@400;600;700&display=swap">
<style>
  :root {
    --page: #eceeee;
    --card: #ffffff;
    --teal: #4fc2a8;
    --ink: #2b2b2b;
    --grey: #6a6a6a;
  }
  * { box-sizing: border-box; margin: 0; padding: 0; }
  html, body {
    width: 1200px; height: 795px; overflow: hidden;
    background: var(--page);
    font-family: "Open Sans", Arial, sans-serif;
    color: var(--ink);
  }
  .canvas {
    position: relative; width: 1200px; height: 795px;
    display: flex; align-items: center; justify-content: center; gap: 50px;
  }
  .card {
    position: relative; width: 520px; height: 297px;
    background: var(--card);
    box-shadow: 0 2px 6px rgba(0,0,0,.08), 0 10px 24px rgba(0,0,0,.06);
  }

  /* Front side */
  .card--front {
    display: flex; flex-direction: column; align-items: center; justify-content: center;
    text-align: center;
  }
  .front__mark {
    width: 50px; height: 50px; border-radius: 50%;
    background: var(--teal); margin-bottom: 10px;
  }
  .front__name {
    font-weight: 700; font-size: 26px; color: var(--teal); line-height: 1.1;
  }
  .front__role {
    margin-top: 8px; font-size: 11px; letter-spacing: .06em;
    text-transform: uppercase; color: var(--grey); word-spacing: .35em;
  }
  .front__contact { margin-top: 8px; font-size: 11.5px; color: var(--grey); }
  .front__web { margin-top: 3px; font-size: 11.5px; color: var(--grey); }
  .front__web span { color: var(--teal); }

  /* Back side */
  .back__photo {
    position: absolute; left: 100px; top: 22px;
    width: 176px; height: 176px; border-radius: 50%;
    background: radial-gradient(circle at 55% 55%, #5a5a5a 0 28%, var(--teal) 29%);
  }
  .back__info { position: absolute; left: 280px; top: 180px; }
  .back__name {
    font-weight: 700; font-size: 28px; color: var(--teal); line-height: 1;
  }
  .back__role { margin-top: 6px; font-size: 10.5px; color: var(--grey); }
  .back__icons { display: flex; gap: 6px; margin-top: 8px; }
  .back__icons span {
    width: 12px; height: 12px; border-radius: 50%; background: var(--teal);
  }
  .back__web {
    margin-top: 8px; font-size: 11px; letter-spacing: .28em; color: var(--grey);
  }
  .back__web b { color: var(--ink); font-weight: 700; }
</style>
</head>
<body>
<main class="canvas">
  <section class="card card--front" aria-label="Card front">
    <div class="front__mark"></div>
    <h1 class="front__name">Tobin Vashley</h1>
    <p class="front__role">Bandleader, Guitarist, Vocalist, Songwriter</p>
    <p class="front__contact">Phone: 646-555-0148, E-mail: tobin@morvalquist.com</p>
    <p class="front__web">www.<span>morvalquist</span>.com</p>
  </section>

  <section class="card card--back" aria-label="Card back">
    <div class="back__photo" role="img" aria-label="Photo of the bandleader in a striped blazer tipping a straw boater hat"></div>
    <div class="back__info">
      <h2 class="back__name">Tobin Vashley</h2>
      <p class="back__role">Bandleader, Guitarist, Vocalist, Songwriter</p>
      <div class="back__icons" aria-label="Social links">
        <span></span><span></span><span></span><span></span><span></span><span></span><span></span><span></span>
      </div>
      <p class="back__web">www.<b>morvalquist</b>.com</p>
    </div>
  </section>
</main>
</body>
</html>
```